Oil Field Service company needs professional business cards

Looking to clean up our current company business cards and look a little more professional. Brenwick Casing Services is a US based company that services the oil field. We deal with engineers, managers and oil rigs....................................................................................................................................................................................................................................................................................................................................................................................................

Target Market(s)

Oil and Gas professionals

Industry/Entity Type

Oil And Gas

Contact Information for Business Card

See attached photo as example

Font styles to use
Sans Serif

Colors
ec1f27

Requirements
Must have
• Company Logo, Name, Title, Cell, Office, Fax, Email.
• See attached photo
Nice to have
• External CRT, Internal CRT, Casing Crews, Torque Turn, Laydown Machine
Should not have
• Do not introduce any new pictures and keep it professional looking

```html
<!DOCTYPE html>
<html lang="en">
<head>
<meta charset="utf-8">
<title>Brenwick Casing Services – Business Card</title>
<link rel="stylesheet" href="https://fonts.googleapis.com/css2?family=Open+Sans:wght@400;600;700;800&display=swap">
<style>
  :root {
    --brand-red: #ec1f27;
    --slate: #4e5a63;
    --slate-dark: #3f4a52;
    --paper: #ffffff;
    --backdrop: #e9e6e1;
    --ink-white: #ffffff;
  }
  * { box-sizing: border-box; margin: 0; padding: 0; }
  html, body {
    width: 1200px; height: 950px; overflow: hidden;
    background: var(--backdrop);
    font-family: "Open Sans", sans-serif;
  }
  .sheet {
    position: relative; width: 1200px; height: 950px;
    display: flex; flex-direction: column; align-items: center; justify-content: center; gap: 60px;
  }
  .card {
    position: relative; width: 630px; height: 360px; overflow: hidden;
    box-shadow: 0 6px 18px rgba(0,0,0,.18);
  }

  /* Front */
  .card-front { background: var(--paper); display: flex; align-items: center; justify-content: center; }
  .wordmark { display: flex; align-items: center; gap: 16px; }
  .wordmark-dot { width: 22px; height: 22px; border-radius: 50%; background: var(--brand-red); }
  .wordmark-name {
    font-weight: 800; font-size: 34px; color: var(--slate-dark); letter-spacing: .5px;
  }

  /* Back */
  .card-back { background: var(--brand-red); color: var(--ink-white); }
  .band {
    position: absolute; left: 0; right: 0; top: 100px; height: 200px;
    background: var(--slate);
  }
  .holder { position: absolute; left: 150px; top: 30px; text-align: left; }
  .holder-name { font-weight: 700; font-size: 24px; line-height: 1.1; }
  .holder-title { font-weight: 400; font-size: 14px; margin-top: 2px; }

  .services {
    position: absolute; right: 30px; top: 18px; list-style: none; text-align: right;
  }
  .services li {
    font-size: 14px; line-height: 22px; display: flex; align-items: center; justify-content: flex-end; gap: 8px;
  }
  .services li::after {
    content: ""; width: 6px; height: 6px; border-radius: 50%; background: var(--brand-red);
  }

  .contacts { position: absolute; left: 26px; bottom: 16px; list-style: none; }
  .contacts li { display: flex; align-items: center; gap: 10px; font-size: 14px; line-height: 22px; }
  .contacts li.cell { font-weight: 700; font-size: 15px; }
  .contacts svg { width: 12px; height: 12px; fill: var(--brand-red); flex: none; }

  .website {
    position: absolute; right: 36px; bottom: 22px;
    font-weight: 700; font-size: 16px; letter-spacing: 4px;
  }
</style>
</head>
<body>
<main class="sheet">

  <section class="card card-front" aria-label="Card front">
    <div class="wordmark">
      <span class="wordmark-dot"></span>
      <span class="wordmark-name">Brenwick Casing Services</span>
    </div>
  </section>

  <section class="card card-back" aria-label="Card back">
    <div class="holder">
      <p class="holder-name">Cody Harlan</p>
      <p class="holder-title">Area Manager</p>
    </div>

    <div class="band">
      <ul class="services">
        <li>External CRT</li>
        <li>Internal CRT</li>
        <li>Casing Crews</li>
        <li>Torque Turn</li>
        <li>Laydown Machine</li>
      </ul>

      <ul class="contacts">
        <li><svg viewBox="0 0 12 12"><path d="M2.5 0.5l2 2.2-1 1.3c.7 1.6 2 2.9 3.6 3.6l1.3-1 2.2 2-1.2 2.1C4.5 10.5 1.5 7.5.4 2.6z"/></svg>(555)210-4400</li>
        <li class="cell"><svg viewBox="0 0 12 12"><path d="M3 0h6a1 1 0 0 1 1 1v10a1 1 0 0 1-1 1H3a1 1 0 0 1-1-1V1a1 1 0 0 1 1-1zm0 1.5v8h6v-8z"/></svg>(555)318-7720</li>
        <li><svg viewBox="0 0 12 12"><path d="M3 0h5v3H3zM1 4h10v6H9v2H3v-2H1zm3 5v2h4V9z"/></svg>(555)210-4410</li>
        <li><svg viewBox="0 0 12 12"><path d="M0 2h12v8H0zm1 1v.4l5 3.3 5-3.3V3z"/></svg>cody@brenwick.com</li>
        <li><svg viewBox="0 0 12 12"><path d="M6 0a4 4 0 0 1 4 4c0 3-4 8-4 8S2 7 2 4a4 4 0 0 1 4-4zm0 2.5A1.5 1.5 0 1 0 6 5.5 1.5 1.5 0 0 0 6 2.5z"/></svg>Redrock Ridge, OK 73990</li>
      </ul>
    </div>

    <p class="website">www.brenwick.com</p>
  </section>

</main>
</body>
</html>
```